birchwell hollow cattle company website

we would like a home page, an about us page, a page for sires, a page for dams, A sale page where we can list progreny for sale and a contact us. on the about us page we would like there to be a family picture. on the sires page we would like to have a picture of each sire, a description beside them and a link to their online profile at northern hereford registry. on the dam page we would like to have a picture of each dam, aswell as a description beside them aswell as a link to the northern hereford registry site. would like the website to very mobile phone friendly as expecting most traffic to be on phone. we would like the website to look and feel very mich like a farm, rustic, barbed wire and other farm feels. we would also like a frozen genetics pages where we can include pictures and descriptions of the sires and dams aswell as a price for embryos and semen. we need to website to be easy to maintain so we can update pictures and information as it changes, we would like there to be a feature so that people can sign up to be on our mailing list by giving us their mailing addess and email and full name
aswell as an area where they can send us a message to contact us.

leaving for work for 3 weeks in the canadian arctic will have limited ability to use the internet

Target Market(s)

other ranchers, farmers, cattlemen,

Industry/Entity Type

farming, agriculture, cattle

Coding

Coded - Design and coding required

Requirements
Must have
• about page, contact page, sires page, dams page, SALE page.
Nice to have
• country/farm vibe, barbed wire, wood,

```html
<!DOCTYPE html>
<html lang="en">
<head>
<meta charset="utf-8">
<title>Birchwell Hollow Cattle Company</title>
<link href="https://fonts.googleapis.com/css2?family=Barlow+Condensed:wght@500;600;700&family=Jost:wght@400;500;600&family=Yellowtail&display=swap" rel="stylesheet">
<style>
:root{
  --ink:#1f1d1b;
  --dark:#1b1a18;
  --gold:#e0a93c;
  --gold-soft:#f3dcae;
  --cream:#f7f1ea;
  --card:#f5efe8;
  --btn:#ebe7e3;
  --white:#ffffff;
  --muted:#3b3835;
}
*{box-sizing:border-box;margin:0;padding:0}
html,body{width:1200px;height:5000px;overflow:hidden}
body{position:relative;background:var(--white);font-family:"Jost",sans-serif;color:var(--ink)}
.abs{position:absolute}
.head{font-family:"Barlow Condensed",sans-serif;font-weight:600;text-transform:uppercase;letter-spacing:.5px;color:var(--ink)}
.script{font-family:"Yellowtail",cursive;color:var(--gold)}
.btn{position:absolute;display:flex;align-items:center;justify-content:center;font-size:12px;font-weight:600;text-transform:uppercase;letter-spacing:.3px;border-radius:4px;background:var(--btn);color:var(--ink);text-decoration:none}
.wordmark{font-family:"Barlow Condensed",sans-serif;font-weight:700;color:var(--white);text-transform:uppercase;text-align:center;line-height:1}

/* hero */
.hero{left:0;top:0;width:1200px;height:800px;background:linear-gradient(180deg,#2d2a27 0%,#4a4034 30%,#8a6d3c 55%,#5b5a2a 78%,#3a3a1c 100%)}
.nav-logo{left:97px;top:22px;width:116px;font-size:19px}
.nav-logo small{display:block;font-size:11px;letter-spacing:3px;margin-top:3px}
.nav{left:404px;top:40px;display:flex;gap:20px;font-size:12px;color:var(--white)}
.nav-cta{left:945px;top:25px;width:156px;height:47px;background:#3d3b39;color:var(--white);font-size:11px}
.hero-script{left:97px;top:250px;font-size:52px}
.hero-title{left:97px;top:322px;font-size:84px;line-height:1;color:var(--white);font-weight:600}
.hero-copy{left:97px;top:421px;width:480px;font-size:15px;line-height:21px;color:var(--white)}
.hero-btn1{left:97px;top:489px;width:181px;height:55px;background:var(--white)}
.hero-btn2{left:289px;top:489px;width:224px;height:55px;background:transparent;border:1px solid var(--white);color:var(--white)}
.badge{left:886px;top:682px;width:224px;height:224px;border-radius:50%;background:#15130f;border:5px solid var(--gold);z-index:3}

/* intro */
.intro-photo{left:0;top:1090px;width:1200px;height:470px;background:linear-gradient(180deg,#ffffff 0%,#e9d3ab 28%,#b98a4f 55%,#8b6a3c 80%,#caa56b 100%)}
.center{left:0;width:1200px;text-align:center}
.intro-script{top:885px;font-size:30px}
.intro-title{top:938px;font-size:38px;line-height:40px}
.intro-copy{top:1040px;left:320px;width:560px;font-size:14px;line-height:21px;text-align:center;color:var(--muted)}
.intro-link{top:1207px;font-size:11px;font-weight:600;text-decoration:underline}

/* program */
.prog-script{top:1620px;font-size:30px}
.prog-title{top:1668px;font-size:38px}
.card{top:1734px;width:299px;height:369px;background:var(--card);border-radius:14px;text-align:center}
.card-img{position:absolute;left:5px;top:5px;width:289px;height:238px;border-radius:12px}
.card h3{position:absolute;top:276px;left:0;width:100%;font-size:16px}
.card p{position:absolute;top:302px;left:40px;width:219px;font-size:10px;line-height:15px;color:var(--muted)}

/* video */
.video{left:0;top:2130px;width:1200px;height:610px;background:linear-gradient(180deg,#f3f1ee 0%,#9ba3a6 18%,#6b5a45 45%,#7a4a26 62%,#a67d45 85%,#cfb47a 100%)}
.play{left:552px;top:2372px;width:96px;height:96px;border-radius:50%;background:var(--gold);opacity:.92}
.video-title{top:2488px;font-size:36px;color:var(--white)}

/* sires */
.cream-band{left:0;top:2860px;width:1200px;height:720px;background:linear-gradient(180deg,#ffffff 0%,#fbf6ef 35%,#f6ede1 100%)}
.sire-dot{left:424px;top:3078px;width:174px;height:174px;border-radius:50%;background:var(--gold-soft);opacity:.75}
.sire-photo{left:183px;top:2847px;width:359px;height:318px;border-radius:20px;background:linear-gradient(160deg,#6f7f4a,#4a3a2a 55%,#8c9a48)}
.sire-script{left:614px;top:2880px;font-size:28px}
.sire-title{left:614px;top:2922px;font-size:38px}
.sire-copy{left:614px;top:2982px;width:420px;font-size:14px;line-height:21px;color:var(--muted)}
.sire-btn{left:614px;top:3070px;width:163px;height:49px}
.qa-title{top:3328px;font-size:58px}
.qa-title span{color:var(--gold)}
.qa-copy{top:3410px;font-size:14px;line-height:21px;color:var(--muted)}
.qa-btn{left:507px;top:3474px;width:186px;height:49px}

/* frozen */
.fz-title{left:150px;top:3765px;font-size:38px;line-height:39px}
.fz-copy{left:150px;top:3862px;width:420px;font-size:14px;line-height:21px;color:var(--muted)}
.fz-copy p+p{margin-top:14px}
.fz-btn{left:151px;top:3987px;width:251px;height:49px}
.fz-photo{left:643px;top:3719px;width:406px;height:359px;border-radius:18px;background:radial-gradient(circle at 55% 45%,#f0b24a,#9a6424 55%,#5a3e1a)}

/* contact */
.contact-bg{left:0;top:4150px;width:1200px;height:520px;background:linear-gradient(180deg,#ffffff 0%,#eef0ec 30%,#c8cdc0 55%,#8f9668 78%,#5c6041 100%)}
.field{position:absolute;background:var(--white);border:1px solid #cfcac4;border-radius:5px;font-size:10px;padding:14px 22px;color:var(--ink)}
.submit{left:109px;top:4472px;width:512px;height:47px;background:#2b2927;color:var(--white);font-size:11px}
.ct-title{left:684px;top:4245px;font-size:38px;line-height:39px}
.ct-copy{left:684px;top:4344px;width:400px;font-size:14px;line-height:21px;color:var(--muted)}
.ct-btn{left:684px;top:4426px;width:186px;height:47px;background:var(--white)}

/* footer */
.footer{left:0;top:4660px;width:1200px;height:340px;background:var(--dark)}
.ft-head{top:4744px;font-size:20px;color:var(--white);font-weight:500}
.ft-list{left:161px;top:4787px;font-size:14px;line-height:31px;color:var(--white)}
.ft-list div{display:flex;align-items:center;gap:8px}
.ft-logo{left:470px;top:4790px;width:260px;font-size:40px}
.ft-logo small{display:block;font-size:18px;letter-spacing:7px;margin-top:8px}
.social{top:4787px;width:38px;height:38px;border-radius:50%;background:#34322f;border:1px solid #4a4744}
.copy{top:4972px;font-size:11px;color:var(--white)}
.to-top{left:1128px;top:4936px;width:40px;height:40px;border-radius:50%;background:var(--gold);display:flex;align-items:center;justify-content:center}
</style>
</head>
<body>

<!-- hero -->
<div class="abs hero" role="img" aria-label="Cattle grazing on an open golden pasture at sunset with hills behind"></div>
<div class="abs wordmark nav-logo">Birchwell Hollow<small>Cattle Company</small></div>
<nav class="abs nav"><span>Home</span><span>About Us</span><span>Sires</span><span>Dams</span><span>Frozen Genetics</span><span>Sale</span><span>Contact</span></nav>
<a class="btn nav-cta">Join Mailing List</a>
<div class="abs script hero-script">Raising Quality</div>
<h1 class="abs head hero-title">Angus Cattle</h1>
<p class="abs hero-copy">Strong genetics, trusted bloodlines, and a deep respect for the land — built through generations of dedicated ranching.</p>
<a class="btn hero-btn1">View Our Sires</a>
<a class="btn hero-btn2">Contact the Ranch</a>

<!-- intro photo & torn edge -->
<div class="abs intro-photo" role="img" aria-label="Rancher and two children walking among a herd of cattle in golden grass"></div>
<svg class="abs" style="left:0;top:760px" width="1200" height="70" viewBox="0 0 1200 70" aria-hidden="true">
  <path d="M0 40 L60 32 L110 44 L170 30 L240 42 L300 28 L360 40 L430 31 L500 45 L560 33 L640 42 L700 30 L770 44 L840 32 L900 40 L960 29 L1030 42 L1100 31 L1160 40 L1200 34 L1200 70 L0 70 Z" fill="#fff"/>
</svg>
<div class="abs badge" role="img" aria-label="Premium quality badge"></div>

<div class="abs center script intro-script">Introduction</div>
<h2 class="abs center head intro-title">Family-Driven. Land-Focused.<br>Quality-Committed.</h2>
<div class="abs intro-copy">
  <p>We are a family-run cattle operation dedicated to producing high-quality Angus genetics for commercial and purebred breeders. Our program focuses on structure, temperament, performance, and maternal strength — ensuring cattle that work in real ranch conditions.</p>
  <p style="margin-top:12px">Every animal we raise reflects our commitment to honest breeding, careful selection, and long-term herd improvement.</p>
</div>
<div class="abs center intro-link">LEARN MORE ABOUT OUR RANCH</div>
<svg class="abs" style="left:0;top:1520px" width="1200" height="60" viewBox="0 0 1200 60" aria-hidden="true">
  <path d="M0 20 L70 30 L140 18 L210 32 L290 20 L360 34 L440 22 L520 33 L600 20 L680 32 L760 19 L840 31 L920 21 L1000 33 L1080 20 L1150 30 L1200 22 L1200 60 L0 60 Z" fill="#fff"/>
</svg>

<!-- program -->
<div class="abs center script prog-script">Our Program</div>
<h2 class="abs center head prog-title">Focused On What Matters Most</h2>
<div class="abs card" style="left:136px">
  <div class="card-img" role="img" aria-label="Young bull standing in a green pasture" style="background:linear-gradient(180deg,#8fa66a,#5a4534 60%,#7f9a52)"></div>
  <h3 class="head">Proven Bloodlines</h3>
  <p>Carefully selected sires and dams backed by strong performance and pedigree data.</p>
</div>
<div class="abs card" style="left:449px">
  <div class="card-img" role="img" aria-label="Cattle grazing on a grassy hillside under cloudy sky" style="background:linear-gradient(180deg,#c9c7bd,#6d7d46 50%,#8a8a4c)"></div>
  <h3 class="head">Functional, Real-World Cattle</h3>
  <p>Raised in practical ranch conditions to ensure durability, fertility, and longevity.</p>
</div>
<div class="abs card" style="left:763px">
  <div class="card-img" role="img" aria-label="Rancher walking toward a herd in a sunlit field" style="background:linear-gradient(180deg,#3f5a36,#7d6a3a 50%,#b38a4e)"></div>
  <h3 class="head">Honest, Straightforward Service</h3>
  <p>We believe in transparency, long-term relationships, and helping fellow cattlemen succeed.</p>
</div>

<!-- video -->
<div class="abs video" role="img" aria-label="Red bull standing on straw inside a steel corral"></div>
<svg class="abs" style="left:0;top:2190px" width="1200" height="40" viewBox="0 0 1200 40" aria-hidden="true">
  <path d="M0 0 L1200 0 L1200 22 L1130 30 L1050 18 L980 28 L900 20 L820 30 L740 19 L660 27 L580 18 L500 29 L420 20 L340 30 L260 19 L180 28 L100 20 L0 26 Z" fill="rgba(243,241,238,.6)"/>
</svg>
<svg class="abs" style="left:0;top:2690px" width="1200" height="60" viewBox="0 0 1200 60" aria-hidden="true">
  <path d="M0 30 L80 18 L160 34 L240 22 L320 36 L400 24 L480 38 L560 22 L640 34 L720 20 L800 35 L880 23 L960 36 L1040 22 L1120 34 L1200 24 L1200 60 L0 60 Z" fill="#fff"/>
</svg>
<div class="abs play"></div>
<svg class="abs" style="left:590px;top:2410px" width="20" height="20" viewBox="0 0 20 20" aria-hidden="true"><path d="M5 3 L17 10 L5 17 Z" fill="#fff"/></svg>
<h2 class="abs center head video-title">Watch Our Video Presentation</h2>

<!-- sires & sale -->
<div class="abs cream-band"></div>
<div class="abs sire-dot"></div>
<div class="abs sire-photo" role="img" aria-label="Dark calf standing by a fence post among yellow wildflowers"></div>
<div class="abs script sire-script">Sires Preview</div>
<h2 class="abs head sire-title">Meet Our Herd Sires</h2>
<p class="abs sire-copy">Our herd sires represent the foundation of our breeding program — selected for performance, structure, and maternal influence.</p>
<a class="btn sire-btn">View Our Sires</a>

<h2 class="abs center head qa-title">Quality Cattle <span>Available</span></h2>
<p class="abs center qa-copy">We offer select progeny throughout the year, including bulls, heifers, and<br>replacement females bred for performance and longevity.</p>
<a class="btn qa-btn">View Sale Listings</a>
<svg class="abs" style="left:0;top:3560px" width="1200" height="50" viewBox="0 0 1200 50" aria-hidden="true">
  <path d="M0 20 L90 30 L170 16 L250 28 L330 18 L420 30 L500 17 L590 29 L670 19 L760 31 L840 18 L930 28 L1010 17 L1100 29 L1200 20 L1200 50 L0 50 Z" fill="#fff"/>
</svg>

<!-- frozen genetics -->
<h2 class="abs head fz-title">Frozen<br>Genetics Available</h2>
<div class="abs fz-copy">
  <p>Embryos and semen from our proven sires and elite donor dams are available in limited quantities.</p>
  <p>This gives breeders access to top-tier genetics while accelerating herd improvement.</p>
</div>
<a class="btn fz-btn">Explore Frozen Genetics</a>
<div class="abs fz-photo" role="img" aria-label="Cow silhouetted in tall grass against golden backlight"></div>

<!-- contact -->
<div class="abs contact-bg" role="img" aria-label="Misty hillside pasture with grazing cattle"></div>
<div class="field" style="left:109px;top:4206px;width:253px;height:49px">First Name *</div>
<div class="field" style="left:371px;top:4206px;width:252px;height:49px">Last Name *</div>
<div class="field" style="left:109px;top:4266px;width:253px;height:49px">Phone Number *</div>
<div class="field" style="left:371px;top:4266px;width:252px;height:49px">Email Address *</div>
<div class="field" style="left:109px;top:4327px;width:514px;height:134px">Message *</div>
<a class="btn submit">Submit</a>
<h2 class="abs head ct-title">Questions?<br>We're Here To Help.</h2>
<p class="abs ct-copy">Whether you're looking for breeding stock, frozen genetics, or more information about our program, we'd be glad to hear from you.</p>
<a class="btn ct-btn" style="font-size:11px">Contact Our Ranch</a>

<!-- footer -->
<div class="abs footer"></div>
<svg class="abs" style="left:0;top:4630px" width="1200" height="40" viewBox="0 0 1200 40" aria-hidden="true">
  <path d="M0 22 L70 14 L150 26 L230 12 L310 24 L390 15 L470 27 L550 13 L630 25 L710 14 L790 26 L870 12 L950 24 L1030 15 L1110 27 L1200 16 L1200 40 L0 40 Z" fill="#1b1a18"/>
</svg>
<div class="abs head ft-head" style="left:161px">Contact Info</div>
<div class="abs ft-list">
  <div><svg width="12" height="14" viewBox="0 0 12 14" aria-hidden="true"><path d="M6 0a5 5 0 0 0-5 5c0 4 5 9 5 9s5-5 5-9a5 5 0 0 0-5-5zm0 7a2 2 0 1 1 0-4 2 2 0 0 1 0 4z" fill="#e0a93c"/></svg>Some goes address link here</div>
  <div><svg width="12" height="12" viewBox="0 0 12 12" aria-hidden="true"><path d="M2 1l2.5 0 1 3-1.5 1a7 7 0 0 0 3 3l1-1.5 3 1 0 2.5a1 1 0 0 1-1 1A10 10 0 0 1 1 2a1 1 0 0 1 1-1z" fill="#e0a93c"/></svg>012.345.6789</div>
  <div><svg width="13" height="10" viewBox="0 0 13 10" aria-hidden="true"><rect width="13" height="10" rx="1" fill="#e0a93c"/><path d="M0 1l6.5 5L13 1" stroke="#1b1a18" stroke-width="1.2" fill="none"/></svg>Connect@example.com</div>
</div>
<div class="abs wordmark ft-logo">Birchwell Hollow<small>Cattle Company</small></div>
<div class="abs head ft-head" style="left:781px">Follow Us</div>
<div class="abs social" style="left:781px"></div>
<div class="abs social" style="left:828px"></div>
<div class="abs social" style="left:872px"></div>
<div class="abs social" style="left:917px"></div>
<div class="abs social" style="left:962px"></div>
<div class="abs social" style="left:1006px"></div>
<div class="abs center copy">© Copyright 2026. Birchwell Hollow All Rights Reserved</div>
<div class="abs to-top"><svg width="12" height="8" viewBox="0 0 12 8" aria-hidden="true"><path d="M1 7l5-5 5 5" stroke="#fff" stroke-width="1.6" fill="none"/></svg></div>

</body>
</html>
```